Harborlight Amusement Collective (HAC)

We need a business card design for Harborlight Amusement Collective. Modern and sleek looking, with all critical information. Open to single or double sided designs, if double sided info needs to be all on one side. The main Logo is Harborlight Amusement collective and must be on the card. The other three logos are for the brands that fall under the group, they might be good on the back.

Industry/Entity Type

Business

```html
<!DOCTYPE html>
<html lang="en">
<head>
<meta charset="utf-8">
<title>Harborlight Amusement Collective – Business Card</title>
<link href="https://fonts.googleapis.com/css2?family=Montserrat:wght@600&family=Open+Sans:wght@400;600;700&display=swap" rel="stylesheet">
<style>
  :root{
    --backdrop:#3b3b3b;
    --card-light:#ededed;
    --brand-blue:#24589b;
    --brand-green:#86a03a;
    --ink:#4a4a4a;
    --rule:#9a9a9a;
    --white:#ffffff;
    --partner-dark:#1f1f1f;
  }
  *{margin:0;padding:0;box-sizing:border-box}
  html,body{width:1200px;height:900px;overflow:hidden}
  body{background:var(--backdrop);position:relative;font-family:"Open Sans",Arial,sans-serif}

  .card{position:absolute;top:170px;width:347px;height:560px;overflow:hidden}
  .card--front{left:259px;background:var(--card-light);text-align:center}
  .card--back{left:631px;background:var(--brand-blue)}

  /* front */
  .brand-mark{position:absolute;left:50%;top:60px;width:42px;height:42px;margin-left:-21px;background:var(--brand-blue)}
  .brand-name{position:absolute;top:150px;left:0;right:0;font-family:"Montserrat",Arial,sans-serif;font-weight:600;color:var(--brand-blue);font-size:17px;line-height:26px;letter-spacing:.5px;text-transform:uppercase}

  .person{position:absolute;top:232px;left:0;right:0}
  .person__name{font-size:19px;letter-spacing:.3px;color:var(--brand-blue);text-transform:uppercase}
  .person__name .surname{color:var(--brand-green)}
  .person__role{font-size:14px;color:var(--ink);margin-top:1px}

  .divider{position:absolute;left:107px;width:148px;height:1px;background:var(--rule)}
  .divider--1{top:285px}.divider--2{top:382px}.divider--3{top:444px}

  .contact{position:absolute;top:294px;left:0;right:0;font-size:14px;line-height:20px;color:var(--ink)}
  .contact .label{color:var(--brand-blue);font-weight:700}
  .contact .web{font-weight:700;color:var(--brand-blue)}
  .contact .web .domain{color:var(--brand-green)}

  .address{position:absolute;top:393px;left:0;right:0;font-size:14px;line-height:20px;color:var(--ink)}

  .partners{position:absolute;top:466px;left:0;right:0;display:flex;flex-direction:column;align-items:center;gap:16px}
  .partners__row{display:flex;justify-content:center;align-items:center;gap:24px}
  .partner{font-weight:700;font-size:14px;line-height:20px;display:flex;align-items:center;gap:6px;white-space:nowrap}
  .partner__dot{width:18px;height:18px;border-radius:50%;display:inline-block;flex:none}
  .partner--tierside{color:var(--partner-dark)}
  .partner--tierside .partner__dot{background:var(--brand-blue)}
  .partner--gatepass{color:var(--brand-blue)}
  .partner--gatepass .partner__dot{background:var(--brand-green)}
  .partner--tickets{color:var(--brand-green)}
  .partner--tickets .partner__dot{background:var(--brand-blue)}

  /* back */
  .back__band{position:absolute;left:0;right:0;top:0;height:185px;background:var(--brand-green)}
  .back__web{position:absolute;left:0;right:0;top:508px;text-align:center;color:var(--white);font-size:16px;letter-spacing:1px}
</style>
</head>
<body>
  <section class="card card--front">
    <div class="brand-mark"></div>
    <div class="brand-name">Harborlight Amusement<br>Collective</div>

    <div class="person">
      <div class="person__name">Marcus <span class="surname">Adler</span></div>
      <div class="person__role">Managing Director</div>
    </div>
    <div class="divider divider--1"></div>

    <div class="contact">
      <div><span class="label">P:</span> 044-987 210 345</div>
      <div><span class="label">M:</span> 044-987 210 346</div>
      <div><span class="label">E:</span> hello@harborlightac.com</div>
      <div class="web">www.<span class="domain">harborlightac</span>.com</div>
    </div>
    <div class="divider divider--2"></div>

    <div class="address">
      <div>48 Quayside Lane</div>
      <div>Port Ellery, 204518.</div>
    </div>
    <div class="divider divider--3"></div>

    <div class="partners">
      <div class="partners__row">
        <div class="partner partner--tierside"><span class="partner__dot"></span>Tierside Hospitality</div>
        <div class="partner partner--gatepass"><span class="partner__dot"></span>gatepass</div>
      </div>
      <div class="partners__row">
        <div class="partner partner--tickets"><span class="partner__dot"></span>HarborTickets</div>
      </div>
    </div>
  </section>

  <section class="card card--back">
    <div class="back__band"></div>
    <div class="back__web">www.harborlightac.com</div>
  </section>
</body>
</html>
```